Business Card Design

We are looking for a business card designed for our landscaping company. We do landscaping installation & Maintenance Services. We would like to see designs that have basic landscaping in background. We also think it is important to have both of our names and phone numbers on the card. We need something that stands out a little whether it is shape of the card or thickness or design.

Business

Bramblewood Yardworks, bramblewoodyard@mailvista.net, Owen Platt 555-273-9104, Daniel Korbin 555-618-3927

```html
<!DOCTYPE html>
<html lang="en">
<head>
<meta charset="utf-8">
<title>Bramblewood Yardworks – Business Card</title>
<link rel="stylesheet" href="https://fonts.googleapis.com/css2?family=Bodoni+Moda:wght@500&family=Open+Sans:wght@400&display=swap">
<style>
  :root {
    --backdrop: #e4e4e4;
    --paper-light: #fafafa;
    --paper-dark: #cfcfcf;
    --rule: #0b0b0b;
    --green: #14a221;
    --green-light: #18b025;
    --green-dark: #0f8e1b;
    --ink: #0d0d0d;
    --name: #dcebdc;
    --contact: #eef6ee;
  }
  * { margin: 0; padding: 0; box-sizing: border-box; }
  html, body { width: 1189px; height: 1200px; overflow: hidden; }
  body { background: var(--backdrop); position: relative; }

  .card {
    position: absolute;
    left: 136px;
    width: 916px;
    height: 524px;
    overflow: hidden;
    box-shadow: 0 4px 12px rgba(0,0,0,0.18);
  }
  .card--first { top: 40px; }
  .card--second { top: 620px; }

  .card__header {
    position: absolute; left: 0; top: 0; width: 100%; height: 235px;
    background: radial-gradient(ellipse at 55% 25%, var(--paper-light) 0%, #e6e6e6 55%, var(--paper-dark) 100%);
  }
  .card__foliage {
    position: absolute; left: 0; top: 50px; width: 310px; height: 185px;
    background: radial-gradient(ellipse at 30% 70%, rgba(170,170,170,0.35) 0%, rgba(190,190,190,0.15) 50%, rgba(210,210,210,0) 75%);
  }
  .card__title {
    position: absolute; left: 0; right: 0; top: 108px;
    text-align: center;
    font-family: "Bodoni Moda", "Didot", serif;
    font-weight: 500;
    font-size: 60px;
    line-height: 1;
    color: var(--ink);
    letter-spacing: -0.5px;
  }

  .card__rule { position: absolute; left: 0; width: 100%; background: var(--rule); }
  .card__rule--top { top: 235px; height: 5px; }
  .card__stripe { position: absolute; left: 0; top: 240px; width: 100%; height: 20px; background: var(--green); }
  .card__rule--bottom { top: 260px; height: 6px; }

  .card__body {
    position: absolute; left: 0; top: 266px; width: 100%; height: 258px;
    background: radial-gradient(ellipse at 52% 70%, var(--green-light) 0%, var(--green) 50%, var(--green-dark) 100%);
  }
  .contact { position: absolute; top: 28px; }
  .contact--left { left: 57px; }
  .contact--right { left: 555px; }
  .contact__name {
    font-family: "Bodoni Moda", "Didot", serif;
    font-weight: 500; font-size: 38px; line-height: 1;
    color: var(--name);
  }
  .contact__phone {
    display: flex; align-items: center; gap: 14px;
    margin-top: 14px;
    font-family: "Open Sans", "Calibri", sans-serif;
    font-size: 27px; line-height: 1;
    color: var(--contact);
  }
  .contact__phone svg { width: 20px; height: 20px; flex: none; }
  .card__email {
    position: absolute; left: 0; right: 0; top: 150px;
    text-align: center;
    font-family: "Open Sans", "Calibri", sans-serif;
    font-size: 26px; line-height: 1;
    color: var(--contact);
  }
</style>
</head>
<body>

<section class="card card--first">
  <div class="card__header">
    <div class="card__foliage" role="img" aria-label="Faint grass and leaf illustration"></div>
    <h1 class="card__title">Bramblewood Yardworks</h1>
  </div>
  <div class="card__rule card__rule--top"></div>
  <div class="card__stripe"></div>
  <div class="card__rule card__rule--bottom"></div>
  <div class="card__body">
    <div class="contact contact--left">
      <div class="contact__name">Owen Platt</div>
      <div class="contact__phone">
        <svg viewBox="0 0 20 20" aria-hidden="true"><rect width="20" height="20" fill="#eef6ee"/><path d="M6 4c1 0 1.5 2.5 1 3.2L6.2 8c.8 1.8 2 3 3.8 3.8l.8-.8c.7-.5 3.2 0 3.2 1 0 1-1 3-2.5 3C7 15 5 11 5 6.5 5 5 5.5 4 6 4z" fill="#14a221"/></svg>
        <span>555-273-9104</span>
      </div>
    </div>
    <div class="contact contact--right">
      <div class="contact__name">Daniel Korbin</div>
      <div class="contact__phone">
        <svg viewBox="0 0 20 20" aria-hidden="true"><rect width="20" height="20" fill="#eef6ee"/><path d="M6 4c1 0 1.5 2.5 1 3.2L6.2 8c.8 1.8 2 3 3.8 3.8l.8-.8c.7-.5 3.2 0 3.2 1 0 1-1 3-2.5 3C7 15 5 11 5 6.5 5 5 5.5 4 6 4z" fill="#14a221"/></svg>
        <span>555-618-3927</span>
      </div>
    </div>
    <div class="card__email">bramblewoodyard@mailvista.net</div>
  </div>
</section>

<section class="card card--second">
  <div class="card__header">
    <div class="card__foliage" role="img" aria-label="Faint grass and leaf illustration"></div>
    <h1 class="card__title">Bramblewood Yardworks</h1>
  </div>
  <div class="card__rule card__rule--top"></div>
  <div class="card__stripe"></div>
  <div class="card__rule card__rule--bottom"></div>
  <div class="card__body">
    <div class="contact contact--left">
      <div class="contact__name">Owen Platt</div>
      <div class="contact__phone">
        <svg viewBox="0 0 20 20" aria-hidden="true"><rect width="20" height="20" fill="#eef6ee"/><path d="M6 4c1 0 1.5 2.5 1 3.2L6.2 8c.8 1.8 2 3 3.8 3.8l.8-.8c.7-.5 3.2 0 3.2 1 0 1-1 3-2.5 3C7 15 5 11 5 6.5 5 5 5.5 4 6 4z" fill="#14a221"/></svg>
        <span>555-273-9104</span>
      </div>
    </div>
    <div class="contact contact--right">
      <div class="contact__name">Daniel Korbin</div>
      <div class="contact__phone">
        <svg viewBox="0 0 20 20" aria-hidden="true"><rect width="20" height="20" fill="#eef6ee"/><path d="M6 4c1 0 1.5 2.5 1 3.2L6.2 8c.8 1.8 2 3 3.8 3.8l.8-.8c.7-.5 3.2 0 3.2 1 0 1-1 3-2.5 3C7 15 5 11 5 6.5 5 5 5.5 4 6 4z" fill="#14a221"/></svg>
        <span>555-618-3927</span>
      </div>
    </div>
    <div class="card__email">bramblewoodyard@mailvista.net</div>
  </div>
</section>

</body>
</html>
```